Coastline Premier Retreats Business Card Design

Design a business card for Coastline Premier Retreats. Look at the website for colors and reference. Card should have logo, name, title, office number, mobile number, email, URL and a tagline like, "Luxury Hotel & Resort Email Marketing" (This might change).

https://www.coastlinepremierretreats.example

The rest I will leave up to your imagination.

Contact Information for Business Card

Logo, name, title, office number, mobile number, email, URL and a tagline like, "Luxury Hotel & Resort Email Marketing" (This might change).

```html
<!DOCTYPE html>
<html lang="en">
<head>
<meta charset="utf-8">
<title>Coastline Premier Retreats – Business Card</title>
<link rel="stylesheet" href="https://fonts.googleapis.com/css2?family=Montserrat:wght@700;800&family=Open+Sans:wght@400;600&display=swap">
<style>
  :root {
    --bg: #393939;
    --card: #1b1b1b;
    --card-deep: #121212;
    --orange: #f07a1e;
    --white: #f4f4f4;
    --muted: #d9d9d9;
  }
  * { box-sizing: border-box; margin: 0; padding: 0; }
  html, body { width: 1200px; height: 801px; overflow: hidden; }
  body {
    background: var(--bg);
    font-family: "Open Sans", Arial, sans-serif;
    position: relative;
  }
  .card {
    position: absolute;
    top: 246px;
    width: 540px;
    height: 309px;
    background: var(--card);
    border-bottom: 3px solid var(--orange);
    border-left: 2px solid var(--orange);
    box-shadow: 0 14px 30px rgba(0,0,0,.45);
    overflow: hidden;
  }
  .card--front { left: 40px; }
  .card--back { left: 620px; }

  .brand {
    position: absolute;
    left: 38px;
    top: 40px;
    display: flex;
    align-items: center;
    gap: 12px;
  }
  .brand__square {
    width: 18px; height: 18px;
    background: var(--orange);
  }
  .brand__name {
    font-family: "Montserrat", Arial, sans-serif;
    font-weight: 800;
    font-size: 24px;
    line-height: 1.1;
    letter-spacing: .5px;
    color: var(--white);
    text-transform: uppercase;
  }

  .person {
    position: absolute;
    left: 38px;
    top: 158px;
    width: 200px;
  }
  .person__name {
    font-family: "Montserrat", Arial, sans-serif;
    font-weight: 800;
    font-size: 19px;
    color: var(--orange);
    text-transform: uppercase;
    letter-spacing: .3px;
  }
  .person__title {
    font-size: 14px;
    color: var(--muted);
    margin-top: 4px;
  }

  .divider {
    position: absolute;
    left: 250px;
    top: 150px;
    width: 1px;
    height: 62px;
    background: var(--orange);
  }

  .contact {
    position: absolute;
    left: 270px;
    top: 146px;
    list-style: none;
  }
  .contact__item {
    display: flex;
    align-items: center;
    gap: 8px;
    font-size: 12.5px;
    color: var(--white);
    line-height: 22px;
  }
  .contact__icon { width: 11px; height: 11px; flex: none; }

  .tagline {
    position: absolute;
    left: 38px;
    bottom: 32px;
    font-size: 14px;
    color: var(--white);
    letter-spacing: .2px;
  }

  .back__texture {
    position: absolute;
    inset: 0;
    background: linear-gradient(120deg, var(--card-deep) 0%, #2a2a2a 45%, var(--card-deep) 70%, #242424 100%);
  }
  .back__label {
    position: absolute;
    right: 40px;
    bottom: 44px;
    display: flex;
    align-items: center;
    gap: 8px;
    padding: 6px 10px;
    background: var(--card);
  }
  .back__label .brand__square { width: 10px; height: 10px; }
  .back__label .brand__name { font-size: 12px; }
</style>
</head>
<body>

  <section class="card card--front" aria-label="Business card front">
    <div class="brand">
      <span class="brand__square"></span>
      <span class="brand__name">Coastline<br>Premier Retreats</span>
    </div>

    <div class="person">
      <p class="person__name">Darren Whitlock</p>
      <p class="person__title">President / CEO</p>
    </div>

    <span class="divider"></span>

    <ul class="contact">
      <li class="contact__item">
        <svg class="contact__icon" viewBox="0 0 12 12"><path fill="#f07a1e" d="M2.3 1l2 2.2-1 1.3c.8 1.6 2 2.8 3.6 3.6l1.3-1 2.2 2-1.2 1.6C5.3 10.4 1.6 6.7 1 3z"/></svg>
        555.014.2290
      </li>
      <li class="contact__item">
        <svg class="contact__icon" viewBox="0 0 12 12"><rect x="1" y="2.5" width="10" height="7" fill="#f07a1e"/><path d="M1 2.5l5 4 5-4" fill="none" stroke="#1b1b1b" stroke-width="1"/></svg>
        info@coastlinepremierretreats.example
      </li>
      <li class="contact__item">
        <svg class="contact__icon" viewBox="0 0 12 12"><circle cx="6" cy="6" r="5" fill="#f07a1e"/><path d="M1 6h10M6 1c2 2.5 2 7.5 0 10M6 1c-2 2.5-2 7.5 0 10" fill="none" stroke="#1b1b1b" stroke-width=".8"/></svg>
        www.coastlinepremierretreats.example
      </li>
    </ul>

    <p class="tagline">Luxury Hotel &amp; Resort Email Marketing</p>
  </section>

  <section class="card card--back" aria-label="Business card back">
    <div class="back__texture" role="img" aria-label="Embossed repeating brand-name pattern in black on black"></div>
    <div class="back__label">
      <span class="brand__square"></span>
      <span class="brand__name">Coastline Premier Retreats</span>
    </div>
  </section>

</body>
</html>
```